tinyTally Resource Book - 10 maths tasks to do outside

I need a 22 (11 pages back to back) page A6 sized book produced to standard for submission to professional printer. Needs to be as .pdf file showing guide lines and allowances for colour bleed. I have text already written and submitted as attachment in a Word file with margins set to A6 size. The theme of the materials is "Nature Play" so using lots of pictures from nature (Australia preferably) and showing lots of patterns in nature (rocks, leaves, flower petals etc). Some of the tasks refer to specific activities, such as "shadows" and "floating" so would be great to illustrate appropriately. The big emphasis is on learning outside the classroom, getting kids to engage actively with nature. I would like to see the pages as full colour - so not white background. The book itself will be spiral bound along the top edge so a margin of at least 1cm will be required at the top of each page (or the bottom of even numbered pages). Book will be printed on plastic laminated matte paper for outdoor use. Font size needs to be big enough to read. Fonts sizes, alignments and page numbers are all different at the moment and need to be standardised. One photo is included in a page as a sample if you can use it, otherwise disregard. Logo for Wattlebrook Numeracy Guild is also included to have as part of the acknowledgements at the back of the book.

Target Market(s)

Book is for early childhood and preschool teachers.

Industry/Entity Type

Education

Font styles to use
Sans Serif

Requirements
Must have
• Colour and appeal.
Nice to have
• Use of natural colours instead of bright catchy colours but that is your call.
Should not have
• American spelling

```html
<!DOCTYPE html>
<html lang="en-AU">
<head>
<meta charset="utf-8">
<title>tinyTally – Outdoor Number Adventures</title>
<link rel="stylesheet" href="https://fonts.googleapis.com/css2?family=Mulish:ital,wght@0,700;1,600&family=Questrial&display=swap">
<style>
  :root {
    --paper: #ffffff;
    --crop: #8a8a8a;
    --title-blue: #2f3a96;
    --title-edge: #ffffff;
    --sponsor-text: #f4f1ee;
    --sky-top: #6f6a78;
    --sky-glow: #f3a35f;
    --sky-gold: #f8d27a;
    --treeline: #2d2420;
    --water-gold: #c98a4e;
    --water-mid: #6e4c3c;
    --water-deep: #3b3738;
  }
  html, body {
    margin: 0;
    padding: 0;
    width: 892px;
    height: 1200px;
    overflow: hidden;
    background: var(--paper);
  }
  .canvas {
    position: relative;
    width: 892px;
    height: 1200px;
    background: var(--paper);
  }
  .crop-marks {
    position: absolute;
    inset: 0;
  }
  .cover-page {
    position: absolute;
    left: 53px;
    top: 60px;
    width: 785px;
    height: 1086px;
    overflow: hidden;
  }
  .cover-photo {
    position: absolute;
    inset: 0;
    background:
      linear-gradient(180deg,
        var(--sky-top) 0%,
        #b7837a 8%,
        var(--sky-glow) 20%,
        var(--sky-gold) 34%,
        #e9a05a 40%,
        var(--treeline) 44%,
        var(--treeline) 49%,
        var(--water-gold) 52%,
        #b0724a 60%,
        var(--water-mid) 72%,
        #4a4040 86%,
        var(--water-deep) 100%);
  }
  .title-block {
    position: absolute;
    left: 0;
    right: 0;
    top: 160px;
    text-align: center;
  }
  .book-title {
    margin: 0;
    font-family: "Mulish", sans-serif;
    font-weight: 700;
    font-size: 108px;
    line-height: 1;
    letter-spacing: -2px;
    color: var(--title-blue);
    -webkit-text-stroke: 3px var(--title-edge);
    paint-order: stroke fill;
  }
  .book-subtitle {
    margin: 6px 0 0;
    font-family: "Mulish", sans-serif;
    font-style: italic;
    font-weight: 600;
    font-size: 33px;
    line-height: 1;
    color: var(--title-blue);
    -webkit-text-stroke: 2px var(--title-edge);
    paint-order: stroke fill;
  }
  .sponsor-mark {
    position: absolute;
    left: 80px;
    top: 908px;
    width: 136px;
    display: flex;
    flex-direction: column;
    align-items: center;
    gap: 8px;
    font-family: "Questrial", sans-serif;
    font-size: 15px;
    line-height: 1.2;
    color: var(--sponsor-text);
    text-align: center;
  }
  .sponsor-mark .dot {
    width: 44px;
    height: 44px;
    border-radius: 50%;
    background: var(--sponsor-text);
  }
  .sponsor-line {
    position: absolute;
    left: 227px;
    top: 930px;
    width: 470px;
    margin: 0;
    font-family: "Questrial", sans-serif;
    font-size: 24px;
    line-height: 33px;
    color: var(--sponsor-text);
  }
  .sponsor-line span {
    display: block;
    text-align: justify;
    text-align-last: justify;
    white-space: nowrap;
  }
</style>
</head>
<body>
<div class="canvas">
  <svg class="crop-marks" width="892" height="1200" viewBox="0 0 892 1200" aria-hidden="true">
    <g stroke="var(--crop)" stroke-width="1" fill="none">
      <path d="M53 0 V40 M0 53 H40 M53 60 V75 M60 53 H75 M53 53 H75 V75"/>
      <path d="M839 0 V40 M852 53 H892 M839 60 V75 M817 53 H832 M817 53 H839 V75"/>
      <path d="M53 1160 V1200 M0 1147 H40 M53 1125 V1140 M60 1147 H75 M53 1125 V1147 H75"/>
      <path d="M839 1160 V1200 M852 1147 H892 M817 1147 H832 M839 1125 V1147 H817"/>
    </g>
  </svg>

  <section class="cover-page">
    <div class="cover-photo" role="img" aria-label="Photograph of a calm lake at sunset, with orange and pink clouds, a silhouetted treeline and hills, and golden light reflected on the rippled water"></div>

    <header class="title-block">
      <h1 class="book-title">tinyTALLY</h1>
      <p class="book-subtitle">Outdoor Number Adventures</p>
    </header>

    <div class="sponsor-mark">
      <span class="dot"></span>
      <span>Wattlebrook Numeracy Guild</span>
    </div>

    <p class="sponsor-line">
      <span>Sponsored by the Riverbend Council</span>
      <span>Outdoor Learning Grants Program and the</span>
      <span>Wattlebrook Numeracy Guild</span>
    </p>
  </section>
</div>
</body>
</html>
```